BOLD & MINIMALIST DESIGN NEEDED

We want a very bold but minimalistic business card design that is impactful and utilizes both sides of the business card. Our current logo is included for your use.

We want bold fonts and good use of negative space. We don't want the logo to overpower the design.

Target Market(s)

Professionals who are building new commercial buildings.

Industry/Entity Type

Construction

Contact Information for Business Card

Name, Title, email, office phone, cell phone, website

Font styles to use
Serif
Sans Serif

Requirements
Must have
• Bold design!

```html
<!DOCTYPE html>
<html lang="en">
<head>
<meta charset="utf-8">
<title>Crestmoor Business Card</title>
<link rel="stylesheet" href="https://fonts.googleapis.com/css2?family=PT+Sans:wght@700&family=Poppins:wght@400&display=swap">
<style>
  :root {
    --page: #d8d3d1;
    --card-top: #f4f1f0;
    --card-bottom: #e6dedd;
    --ink: #0b0c0e;
    --green: #8cc63f;
    --green-light: #c4e49a;
    --white: #ffffff;
    --rule: #6b6b6b;
  }
  html, body {
    margin: 0;
    width: 1200px;
    height: 900px;
    overflow: hidden;
    background: var(--page);
  }
  .card {
    position: absolute;
    left: 55px;
    top: 113px;
    width: 1090px;
    height: 673px;
    background: linear-gradient(160deg, var(--card-top), var(--card-bottom));
    overflow: hidden;
    box-shadow: 0 18px 40px rgba(0,0,0,0.18);
  }
  .card__bands {
    position: absolute;
    inset: 0;
    width: 1090px;
    height: 673px;
  }
  .holder {
    position: absolute;
    left: 68px;
    top: 98px;
  }
  .holder__name {
    margin: 0;
    font-family: "PT Sans", sans-serif;
    font-weight: 700;
    font-size: 46px;
    line-height: 1;
    color: var(--ink);
    letter-spacing: 0.5px;
    padding-bottom: 6px;
    border-bottom: 2px solid var(--rule);
  }
  .holder__title {
    margin: 6px 0 0;
    font-family: "Poppins", sans-serif;
    font-size: 27px;
    line-height: 1.2;
    color: var(--ink);
  }
  .brand {
    position: absolute;
    left: 516px;
    top: 40px;
    width: 525px;
    text-align: center;
  }
  .brand__mark {
    display: block;
    width: 110px;
    height: 110px;
    margin: 0 auto 56px;
    background: var(--green);
  }
  .brand__name {
    margin: 0;
    font-family: "PT Sans", sans-serif;
    font-weight: 700;
    font-size: 84px;
    line-height: 1;
    color: var(--ink);
    letter-spacing: 1px;
  }
  .contact {
    position: absolute;
    margin: 0;
    padding: 0;
    list-style: none;
    font-family: "Poppins", sans-serif;
    font-size: 33px;
    line-height: 40px;
  }
  .contact li {
    display: flex;
    align-items: center;
    gap: 16px;
  }
  .contact--phones {
    right: 580px;
    top: 558px;
    color: var(--white);
  }
  .contact--online {
    left: 568px;
    top: 560px;
    color: var(--ink);
  }
  .contact--online li { flex-direction: row; }
  .icon {
    width: 30px;
    height: 30px;
    flex: none;
  }
</style>
</head>
<body>
  <main class="card">
    <svg class="card__bands" viewBox="0 0 1090 673" aria-hidden="true">
      <defs>
        <linearGradient id="greenFade" x1="0" y1="0" x2="1" y2="0">
          <stop offset="0" stop-color="var(--green)"/>
          <stop offset="0.55" stop-color="var(--green)"/>
          <stop offset="1" stop-color="var(--green-light)"/>
        </linearGradient>
      </defs>
      <polygon points="0,588 544,384 544,390 0,596" fill="var(--ink)"/>
      <polygon points="0,600 544,407 544,673 0,673" fill="var(--ink)"/>
      <polygon points="544,384 1020,560 1020,566 544,391" fill="url(#greenFade)"/>
      <polygon points="544,407 1090,590 1090,673 544,673" fill="url(#greenFade)"/>
    </svg>

    <header class="holder">
      <h1 class="holder__name">DANIEL REEVES</h1>
      <p class="holder__title">MANAGING DIRECTOR</p>
    </header>

    <div class="brand">
      <span class="brand__mark"></span>
      <p class="brand__name">CRESTMOOR</p>
    </div>

    <ul class="contact contact--phones">
      <li>021-555 010 246
        <svg class="icon" viewBox="0 0 30 30" aria-label="Office phone">
          <rect x="1.5" y="1.5" width="27" height="27" rx="3" fill="none" stroke="var(--green)" stroke-width="2"/>
          <path d="M10 8c1 0 2 2.5 2 3.2 0 .8-1.4 1.2-1.2 2 .6 2 2.3 3.8 4.2 4.6.8.3 1.3-1.1 2-1.1.8 0 3.2 1.2 3.2 2.1 0 1.2-1.4 2.4-2.6 2.4C12.8 21.2 8 16.6 8 11c0-1.3 1-3 2-3z" fill="var(--green)"/>
        </svg>
      </li>
      <li>021-555 010 381
        <svg class="icon" viewBox="0 0 30 30" aria-label="Mobile phone">
          <rect x="1.5" y="1.5" width="27" height="27" rx="3" fill="none" stroke="var(--green)" stroke-width="2"/>
          <rect x="10" y="7" width="10" height="16" rx="1.5" fill="none" stroke="var(--white)" stroke-width="1.8"/>
          <line x1="13" y1="20" x2="17" y2="20" stroke="var(--white)" stroke-width="1.5"/>
        </svg>
      </li>
    </ul>

    <ul class="contact contact--online">
      <li>
        <svg class="icon" viewBox="0 0 30 30" aria-label="Email">
          <rect x="1.5" y="1.5" width="27" height="27" rx="3" fill="none" stroke="var(--ink)" stroke-width="2"/>
          <rect x="7" y="9" width="16" height="12" fill="var(--ink)"/>
          <path d="M7 9l8 7 8-7" fill="none" stroke="var(--green)" stroke-width="1.5"/>
        </svg>
        info@crestmoor.com
      </li>
      <li>
        <svg class="icon" viewBox="0 0 30 30" aria-label="Website">
          <rect x="1.5" y="1.5" width="27" height="27" rx="3" fill="none" stroke="var(--ink)" stroke-width="2"/>
          <circle cx="15" cy="15" r="8" fill="none" stroke="var(--ink)" stroke-width="1.6"/>
          <ellipse cx="15" cy="15" rx="3.5" ry="8" fill="none" stroke="var(--ink)" stroke-width="1.4"/>
          <line x1="7" y1="15" x2="23" y2="15" stroke="var(--ink)" stroke-width="1.4"/>
        </svg>
        www.crestmoor.com
      </li>
    </ul>
  </main>
</body>
</html>
```